Veltrane Group Business Card Design

The CEO is looking for a new trendy look for his business card.
You can stay with current branding or come up with something new/creative. It can be 3D, including Medical Office buildings. You can use our logo in a variety of colors. Please include name, title, company name, company website, email address, cell number

Target Market(s)

Real Estate Development and Construction

Industry/Entity Type

Health care real estate

Contact Information for Business Card

Rohesh Kamdar, CEO M-604.781.2249 E-roheshkamdar@veltrane.com Address:4180 Lindqvist Ave, Tampa, FL 33482 www.veltrane.com

Font styles to use
Other font styles liked:
• Be creative

Requirements
Must have
• Creative, trendy look
Nice to have
• Please go to our website to get a feel- www. veltrane.com
Should not have
• small fonts

```html
<!DOCTYPE html>
<html lang="en">
<head>
<meta charset="utf-8">
<title>Veltrane Group — Business Card</title>
<link href="https://fonts.googleapis.com/css2?family=Montserrat:wght@400;700;800&display=swap" rel="stylesheet">
<style>
  :root {
    --brand-red: #b21f29;
    --ink: #2b2b2b;
    --card: #ffffff;
    --backdrop: #e4e4e6;
  }
  * { box-sizing: border-box; margin: 0; padding: 0; }
  html, body {
    width: 1200px; height: 900px; overflow: hidden;
    background: var(--backdrop);
    font-family: "Montserrat", sans-serif;
  }
  .sheet {
    width: 1200px; height: 900px;
    display: flex; flex-direction: column;
    align-items: center; justify-content: center; gap: 40px;
  }
  .card {
    position: relative;
    width: 640px; height: 366px;
    background: var(--card);
    border-radius: 22px;
    box-shadow: 0 6px 18px rgba(0,0,0,.12);
    overflow: hidden;
  }
  .wordmark {
    color: var(--brand-red);
    font-weight: 800;
    letter-spacing: -1px;
    line-height: 1;
    white-space: nowrap;
  }
  .card--front { display: flex; align-items: center; justify-content: center; }
  .card--front .wordmark { font-size: 64px; }

  .card--back .wordmark {
    position: absolute; right: 42px; top: 54px;
    font-size: 44px;
  }
  .divider {
    position: absolute; left: 42px; right: 42px; top: 236px;
    height: 2px; background: var(--brand-red);
  }
  .person { position: absolute; left: 42px; top: 172px; }
  .person__name {
    color: var(--brand-red); font-weight: 800; font-size: 26px; letter-spacing: .5px;
  }
  .person__title { color: var(--ink); font-size: 17px; margin-top: 4px; }
  .address {
    position: absolute; right: 42px; top: 176px;
    text-align: right; color: var(--ink); font-size: 15px; line-height: 1.45;
  }
  .contacts { position: absolute; left: 42px; top: 254px; list-style: none; }
  .contacts li {
    display: flex; align-items: center; gap: 10px;
    color: var(--ink); font-size: 16px; line-height: 1.6;
  }
  .contacts svg { width: 14px; height: 14px; flex: none; }
</style>
</head>
<body>
<main class="sheet">
  <section class="card card--front">
    <span class="wordmark">Veltrane Group</span>
  </section>

  <section class="card card--back">
    <span class="wordmark">Veltrane Group</span>
    <div class="person">
      <p class="person__name">ROHESH KAMDAR</p>
      <p class="person__title">CEO</p>
    </div>
    <p class="address">4180 Lindqvist Ave,<br>Tampa, FL 33482</p>
    <div class="divider"></div>
    <ul class="contacts">
      <li>
        <svg viewBox="0 0 14 14" aria-hidden="true"><rect x="3.5" y="1" width="7" height="12" rx="1.5" fill="none" stroke="#b21f29" stroke-width="1.4"/><circle cx="7" cy="11" r=".8" fill="#b21f29"/></svg>
        604.781.2249
      </li>
      <li>
        <svg viewBox="0 0 14 14" aria-hidden="true"><rect x="1" y="3" width="12" height="8" fill="#b21f29"/><path d="M1 3l6 5 6-5" fill="none" stroke="#fff" stroke-width="1.2"/></svg>
        roheshkamdar@veltrane.com
      </li>
      <li>
        <svg viewBox="0 0 14 14" aria-hidden="true"><circle cx="7" cy="7" r="6" fill="#b21f29"/><path d="M1 7h12M7 1c-3 3-3 9 0 12M7 1c3 3 3 9 0 12" fill="none" stroke="#fff" stroke-width=".9"/></svg>
        www.veltrane.com
      </li>
    </ul>
  </section>
</main>
</body>
</html>
```